All Natural Mosquito Repellent

My company, BrightPebble Company has created an all natural mosquito repellent. I already have other all natural products that I have developed and created labels for. I will include a copy of that label so you have something to work from. I will need two labels. One for the front of the bottle and one for the back. The back label will need space for a UPC. The labels need to be 63mm (H) x 39mm (W)

Target Market(s)

Consumers, Organic, People who like natural products

Font styles to use
Other font styles liked:
• A combination of both Serif and Sans Serif

Requirements
Must have
• Use the words Organic, All Natural, Travel size, made in the USA label
Nice to have
• tag line: Don't beat them off. Spray them away.

```html
<!DOCTYPE html>
<html lang="en">
<head>
<meta charset="utf-8">
<title>BrightPebble Co. – All Natural Mosquito Repellent Labels</title>
<link href="https://fonts.googleapis.com/css2?family=Open+Sans:ital,wdth,wght@0,75..100,300..800;1,75..100,300..800&display=swap" rel="stylesheet">
<style>
  :root {
    --bg-light: #f2f2f2;
    --bg-dark: #c9c9c9;
    --forest: #0f3d1c;
    --forest-deep: #0a2e14;
    --forest-mid: #1c5a2a;
    --lime: #8cc43f;
    --ember: #e2401f;
    --ember-dark: #b8300f;
    --white: #ffffff;
  }
  * { margin: 0; padding: 0; box-sizing: border-box; }
  html, body { width: 1200px; height: 1200px; overflow: hidden; }
  body {
    background: radial-gradient(circle at 50% 40%, var(--bg-light) 0%, var(--bg-dark) 100%);
    font-family: "Open Sans", sans-serif;
    color: var(--white);
    position: relative;
  }
  .label {
    position: absolute;
    top: 280px;
    width: 400px;
    height: 640px;
    background: var(--forest);
    border: 5px solid var(--lime);
    border-radius: 10px;
    overflow: hidden;
  }
  .label--front { left: 170px; }
  .label--back { left: 630px; }

  /* front */
  .brand-name {
    position: absolute; top: 138px; width: 100%; text-align: center;
    font-size: 26px; font-weight: 400; letter-spacing: 0.5px; color: var(--white);
  }
  .forest-band {
    position: absolute; left: 0; top: 196px; width: 100%; height: 110px;
    background: linear-gradient(180deg, var(--forest) 0%, var(--forest-mid) 55%, var(--forest-deep) 100%);
  }
  .product-title {
    position: absolute; top: 246px; width: 100%; text-align: center;
    font-size: 21px; line-height: 22px; font-weight: 800; font-style: italic;
    color: var(--ember); text-transform: uppercase;
    text-shadow: -1.5px -1.5px 0 var(--white), 1.5px -1.5px 0 var(--white),
                 -1.5px 1.5px 0 var(--white), 1.5px 1.5px 0 var(--white);
  }
  .product-meta {
    position: absolute; top: 304px; width: 100%; text-align: center;
    font-size: 11px; font-weight: 400; color: var(--white); letter-spacing: 0.2px;
  }
  .swoosh { position: absolute; left: 140px; width: 120px; height: 20px; }
  .swoosh--top { top: 352px; }
  .swoosh--bottom { top: 446px; }
  .tagline {
    position: absolute; top: 388px; width: 100%; text-align: center;
    font-size: 22px; line-height: 26px; font-style: italic; font-weight: 500;
    font-stretch: 80%; color: var(--white);
  }
  .shield-badge {
    position: absolute; left: 172px; top: 504px; width: 56px; height: 62px;
    background: linear-gradient(180deg, #e8e8e8 0%, #9a9a9a 100%);
    clip-path: polygon(0 8%, 50% 0, 100% 8%, 100% 45%, 50% 100%, 0 45%);
  }
  .volume {
    position: absolute; left: 318px; top: 544px;
    font-size: 12px; font-weight: 700; color: var(--white);
  }
  .base-band { position: absolute; left: 0; bottom: 0; width: 100%; height: 72px; }
  .origin {
    position: absolute; bottom: 14px; width: 100%; text-align: center;
    font-size: 17px; font-weight: 400; color: var(--white);
  }
  .protection-sticker {
    position: absolute; left: 8px; top: 544px;
    transform: rotate(-18deg);
    font-size: 13px; line-height: 13px; font-weight: 800; text-align: center;
    color: var(--white); text-transform: uppercase;
    text-shadow: -1px -1px 0 var(--ember-dark), 1px -1px 0 var(--ember-dark),
                 -1px 1px 0 var(--ember-dark), 1px 1px 0 var(--ember-dark);
  }

  /* back */
  .info-section { position: absolute; left: 0; width: 100%; text-align: center; }
  .info-heading {
    display: inline-block; border: 1.5px solid var(--white); border-radius: 3px;
    padding: 2px 8px; font-size: 11.5px; font-weight: 700; text-transform: uppercase;
  }
  .info-text {
    margin: 8px auto 0; width: 300px; font-size: 8.3px; line-height: 11px; font-weight: 400;
  }
  .info-section--directions { top: 42px; }
  .info-section--precaution { top: 157px; }
  .info-section--ingredients { top: 246px; }
  .info-section--storage { top: 336px; }
  .address {
    position: absolute; left: 92px; top: 430px; width: 200px;
  }
  .address-title { font-size: 14px; font-weight: 700; margin-left: 8px; }
  .address-text { font-size: 11px; line-height: 15px; margin-top: 6px; }
  .recycle-icon { position: absolute; left: 26px; top: 552px; width: 46px; height: 46px; }
  .upc-box {
    position: absolute; left: 102px; top: 538px; width: 260px; height: 78px;
    border: 2px solid var(--white);
    display: flex; align-items: center; justify-content: center;
    font-size: 22px; font-weight: 700;
  }
</style>
</head>
<body>

<section class="label label--front">
  <div class="brand-name">BRIGHTPEBBLE CO.</div>

  <div class="forest-band" role="img" aria-label="Silhouette of a pine forest treeline"></div>

  <h1 class="product-title">All Natural<br>Mosquito Repellent</h1>
  <div class="product-meta">ORGANIC &nbsp;●&nbsp; TRAVEL SIZE</div>

  <svg class="swoosh swoosh--top" viewBox="0 0 120 20" aria-hidden="true">
    <path d="M8 18 Q60 -2 112 10 Q60 4 8 18 Z" fill="#ffffff"/>
  </svg>
  <p class="tagline">“Don't beat them off<br>Spray them away”</p>
  <svg class="swoosh swoosh--bottom" viewBox="0 0 120 20" aria-hidden="true">
    <path d="M8 2 Q60 22 112 10 Q60 16 8 2 Z" fill="#ffffff"/>
  </svg>

  <div class="shield-badge" role="img" aria-label="Shield badge with a mosquito illustration"></div>
  <div class="volume">50 ML</div>

  <svg class="base-band" viewBox="0 0 400 72" preserveAspectRatio="none" aria-hidden="true">
    <path d="M0 22 Q200 -12 400 22 L400 72 L0 72 Z" fill="#8cc43f"/>
  </svg>
  <div class="origin">Made in the USA</div>
  <div class="protection-sticker">12 Hour<br>Protection</div>
</section>

<section class="label label--back">
  <div class="info-section info-section--directions">
    <h2 class="info-heading">Direction for use:</h2>
    <p class="info-text">There are many variations of passages of Lorem Ipsum available, but the majority have suffered alteration in some form, by injected humour, or randomised words which don't look even slightly believable. If you are going to use a passage of Lorem Ipsum, you need to be sure there isn't anything embarrassing hidden in the middle of text.</p>
  </div>
  <div class="info-section info-section--precaution">
    <h2 class="info-heading">Precaution:</h2>
    <p class="info-text">There are many variations of passages of Lorem Ipsum available, but the majority have suffered alteration in some form, by injected humour, or randomised words which don't look even slightly believable.</p>
  </div>
  <div class="info-section info-section--ingredients">
    <h2 class="info-heading">Ingredients:</h2>
    <p class="info-text">There are many variations of passages of Lorem Ipsum available, but the majority have suffered alteration in some form, by injected humour, or randomised words which don't look even slightly believable.</p>
  </div>
  <div class="info-section info-section--storage">
    <h2 class="info-heading">Storage:</h2>
    <p class="info-text">Store in a cool and dry place. Place empty container in<br>trsh or recycle.</p>
  </div>

  <div class="address">
    <div class="address-title">Company Address:</div>
    <p class="address-text">Lorem Ipsum is simply dummy<br>text of the printing and typesetting<br>industry.</p>
  </div>

  <svg class="recycle-icon" viewBox="0 0 46 46" role="img" aria-label="Recycling symbol">
    <g fill="none" stroke="#ffffff" stroke-width="4" stroke-linejoin="round" stroke-linecap="round">
      <path d="M14 20 L20 9 Q23 4 26 9 L30 16"/>
      <path d="M34 24 L40 34 Q42 39 36 39 L28 39"/>
      <path d="M18 39 L9 39 Q4 39 7 34 L10 28"/>
    </g>
    <g fill="#ffffff">
      <path d="M26 16 L35 17 L31 9 Z"/>
      <path d="M29 34 L24 39 L29 44 Z"/>
      <path d="M6 26 L14 24 L12 32 Z"/>
    </g>
  </svg>

  <div class="upc-box">UPC</div>
</section>

</body>
</html>
```